sydney wedding photography business needs a business card design

we need a business card design for a sydney based wedding photography and videography business. our business name is :golden hour studio and film. our target clients are 24-35 yrs female. our style is candid, organic, natural, dynamic. we are a team of young photographers and videographers, and help brides to create memories that they will cherish for the rest of their lives. the logo will be provided. we want an elegant design that reflects our style, and also want to give a great impression to our clients that we are one of the best studios in sydney and our brand means quality and premium service.

Target Market(s)

bride to be, 24-35 years old, living in sydney and surrunding areas

Industry/Entity Type

Wedding Photography

Contact Information for Business Card

address: 57 tarrant street, glenmore nsw 2047
mobile: 0431872259
phone: (02) 9163 2408
info@tidewillowstudio.net.au
www.tidewillowstudio.net.au
facebook:tidewillowweddings
instagram:tidewillowweddings

Font styles to use
Serif
Sans Serif

Requirements
Nice to have
• maybe add my slogan"memories beyond eternity" if the layout looks good
Should not have
• no black color, not good idea for wedding biz card

```html
<!DOCTYPE html>
<html lang="en">
<head>
<meta charset="utf-8">
<title>Golden Hour Studio and Film – Business Card</title>
<link href="https://fonts.googleapis.com/css2?family=Open+Sans:wght@300;400;600;700&display=swap" rel="stylesheet">
<style>
  :root {
    --navy: #0a0c33;
    --slate: #263640;
    --band-navy: #1e2248;
    --gold: #d29a1a;
    --gold-soft: #e8c66a;
    --rose: #a8705a;
    --white: #ffffff;
    --text: #0a0c33;
  }
  * { margin: 0; padding: 0; box-sizing: border-box; }
  html, body { width: 1200px; height: 1200px; overflow: hidden; background: var(--white); }
  body { position: relative; font-family: "Open Sans", Arial, sans-serif; }

  .card {
    position: absolute;
    left: 210px;
    width: 780px;
    height: 445px;
    border: 13px solid var(--navy);
    background: var(--white);
    overflow: hidden;
  }
  .card--front { top: 140px; }
  .card--back { top: 649px; }

  .pattern {
    position: absolute;
    left: 0; right: 0;
    background:
      radial-gradient(ellipse 40% 70% at 30% 60%, rgba(210,154,26,0.22), transparent 70%),
      radial-gradient(ellipse 35% 70% at 62% 40%, rgba(168,112,90,0.20), transparent 70%),
      radial-gradient(ellipse 35% 70% at 90% 70%, rgba(232,198,106,0.25), transparent 70%),
      linear-gradient(160deg, #b3b3b3 0%, #dcdcdc 35%, #f2f2f2 65%, #ffffff 100%);
  }
  .pattern--light {
    background:
      radial-gradient(ellipse 35% 80% at 20% 40%, rgba(232,198,106,0.25), transparent 70%),
      radial-gradient(ellipse 35% 80% at 55% 60%, rgba(168,112,90,0.18), transparent 70%),
      radial-gradient(ellipse 35% 80% at 88% 40%, rgba(232,198,106,0.25), transparent 70%),
      #fbfbfb;
  }

  .front__pattern-top { top: 0; height: 167px; }
  .front__band { position: absolute; left: 0; right: 0; top: 167px; height: 96px; background: var(--slate); }
  .front__band-navy { position: absolute; left: 0; right: 0; top: 263px; height: 34px; background: var(--band-navy); }
  .front__pattern-bottom { top: 297px; bottom: 0; }

  .brand {
    position: absolute;
    left: 0; right: 0;
    text-align: center;
    color: var(--gold);
    font-weight: 600;
    text-transform: uppercase;
    line-height: 1;
    white-space: nowrap;
  }
  .brand__main { top: 193px; font-size: 44px; letter-spacing: 5px; }
  .brand__sub { top: 268px; font-size: 22px; letter-spacing: 11px; padding-left: 11px; line-height: 24px; }

  .back__pattern-top { top: 0; height: 107px; }
  .back__band { position: absolute; left: 0; right: 0; top: 107px; height: 100px; background: var(--slate); }
  .back__pattern-fade { top: 207px; height: 44px; opacity: 0.7; }

  .person-name {
    position: absolute;
    left: 0; right: 0; top: 128px;
    text-align: center;
    color: var(--white);
    font-size: 40px;
    font-weight: 300;
    letter-spacing: 8px;
    line-height: 1;
  }
  .person-name strong { font-weight: 700; }
  .person-role {
    position: absolute;
    left: 0; right: 0; top: 180px;
    text-align: center;
    color: var(--white);
    font-size: 12px;
    letter-spacing: 3.2px;
  }

  .contact {
    position: absolute;
    color: var(--text);
    font-weight: 600;
    font-size: 15.5px;
    line-height: 20px;
  }
  .contact svg { position: absolute; left: -24px; top: 2px; width: 15px; height: 15px; fill: var(--navy); }
  .contact--address { left: 65px; top: 288px; }
  .contact--web { left: 62px; top: 349px; }
  .contact--phone { left: 495px; top: 287px; }
  .contact--email { left: 495px; top: 343px; }
</style>
</head>
<body>

<section class="card card--front">
  <div class="pattern front__pattern-top" role="img" aria-label="Gold and rose geometric circle lattice pattern"></div>
  <div class="front__band"></div>
  <div class="front__band-navy"></div>
  <div class="pattern pattern--light front__pattern-bottom" role="img" aria-label="Gold and rose geometric circle lattice pattern"></div>
  <h1 class="brand brand__main">golden hour</h1>
  <p class="brand brand__sub">studio and film</p>
</section>

<section class="card card--back">
  <div class="pattern back__pattern-top" role="img" aria-label="Gold and rose geometric circle lattice pattern"></div>
  <div class="back__band"></div>
  <div class="pattern pattern--light back__pattern-fade" role="img" aria-label="Faded geometric lattice pattern strip"></div>
  <h2 class="person-name">NA<strong>ME</strong></h2>
  <p class="person-role">PHOTOGRAPHER&amp;VEDIOGRAPHER</p>

  <div class="contact contact--address">
    <svg viewBox="0 0 24 24" aria-hidden="true"><path d="M12 1a8 8 0 0 0-8 8c0 6 8 14 8 14s8-8 8-14a8 8 0 0 0-8-8zm0 11a3 3 0 1 1 0-6 3 3 0 0 1 0 6z"/></svg>
    57 tarrant street,<br>glenmore nsw 2047
  </div>

  <div class="contact contact--web">
    <svg viewBox="0 0 24 24" aria-hidden="true"><path d="M12 1a11 11 0 1 0 0 22 11 11 0 0 0 0-22zm0 2a9 9 0 0 1 6.7 3H15l-2 2-3-1-2 3 2 3v4l2 3a9 9 0 0 1-7.5-13.5L7 9l2-1-1-3a9 9 0 0 1 4-2zm7.8 5A9 9 0 0 1 16 20l1-5-2-2 2-3z"/></svg>
    www.tidewillowstudio.net.au<br>
    facebook:tidewillowweddings<br>
    instagram:tidewillowweddings
  </div>

  <div class="contact contact--phone">
    <svg viewBox="0 0 24 24" aria-hidden="true"><path d="M6.6 10.8a15 15 0 0 0 6.6 6.6l2.2-2.2a1 1 0 0 1 1-.25 11 11 0 0 0 3.6.6 1 1 0 0 1 1 1V20a1 1 0 0 1-1 1A17 17 0 0 1 3 4a1 1 0 0 1 1-1h3.5a1 1 0 0 1 1 1 11 11 0 0 0 .6 3.6 1 1 0 0 1-.25 1z"/></svg>
    mobile: 0431872259<br>
    phone: (02) 9163 2408
  </div>

  <div class="contact contact--email">
    <svg viewBox="0 0 24 24" aria-hidden="true"><path d="M2 5h20v14H2zm2 2v.5l8 5.5 8-5.5V7zm0 3v7h16v-7l-8 5.5z"/></svg>
    info@tidewillowstudio.net.au
  </div>
</section>

</body>
</html>
```